Business Card & Email Signature Design || Upmarket + Luxury

Rima Vale Honey, a New Zealand Manuka Honey company needs a Business Card & Email Signature design.

Our logo's are attached in Gold & Black versions, feel free to be creative with how you use the logo and it's patterns in your design.

Style:
- Looking for an Elegant, Luxurious, Upmarket feel.
- Black/Matte Black Card, Gold Foil, UV Embossing

Information to Add:

- Logo
- Company Name: Rima Vale Honey
- Name: Martin Holloway
- Title: Creative Director
- Phone: +64 2815 96 417
- Email: martin@rimavalehoney.example.nz
- Website: www.rimavalehoney.example.nz

- Socials: ***For email Signature Only***
- Facebook: https://www.facebook.com/rimavalehoney/
- Instagram: https://www.instagram.com/rimavalehoney/

Target Market(s)

Asia/Europe Luxury, Upmarket

Contact Information for Business Card

- Logo
- Name: Martin Holloway
- Phone: +64 2815 96 417

Font styles to use
Other font styles liked:
• Champagne & Limousines (Attached)

Requirements
Must have
• Business Card & Email Signature Design.

Looking for a Sleek, Luxury, Upmarket Design.

```html
<!DOCTYPE html>
<html lang="en">
<head>
<meta charset="utf-8">
<title>Rima Vale Honey — Business Card</title>
<link href="https://fonts.googleapis.com/css2?family=Montserrat:wght@400;600;700&display=swap" rel="stylesheet">
<style>
  :root {
    --stage: #1c1c1c;
    --card: #121212;
    --card-edge: #1a1a1a;
    --gold: #e3c06a;
    --ink-light: #e9e9e9;
    --pattern-light: #4a4a4a;
    --pattern-mid: #2c2c2c;
    --pattern-dark: #171717;
    --emboss-light: #2e2e2e;
    --emboss-mid: #222222;
  }
  * { box-sizing: border-box; margin: 0; padding: 0; }
  html, body { width: 1200px; height: 780px; overflow: hidden; }
  body {
    background: var(--stage);
    font-family: "Montserrat", sans-serif;
    display: flex;
    align-items: center;
    justify-content: center;
    gap: 40px;
  }
  .card {
    position: relative;
    width: 540px;
    height: 308px;
    background: var(--card);
    border: 1px solid var(--card-edge);
    box-shadow: 0 18px 40px rgba(0,0,0,0.55);
    overflow: hidden;
  }

  /* Back of card */
  .card-back__pattern {
    position: absolute;
    inset: 0;
    background:
      radial-gradient(ellipse 70% 80% at 10% 95%, var(--pattern-light) 0%, transparent 70%),
      linear-gradient(30deg, var(--pattern-mid) 0%, #222 45%, var(--pattern-dark) 100%);
  }
  .card-back__mark {
    position: absolute;
    right: 30px;
    top: 126px;
    display: flex;
    align-items: center;
    gap: 6px;
    color: var(--gold);
    font-size: 9px;
    font-weight: 600;
    letter-spacing: 0.18em;
    text-transform: uppercase;
  }
  .dot {
    width: 8px; height: 8px;
    border-radius: 50%;
    background: var(--gold);
    flex: none;
  }

  /* Front of card */
  .card-front__emboss {
    position: absolute;
    right: 24px;
    top: 24px;
    width: 250px;
    height: 260px;
    border-radius: 46% 54% 50% 50% / 40% 40% 60% 60%;
    background: radial-gradient(ellipse at 55% 45%, var(--emboss-light) 0%, var(--emboss-mid) 45%, var(--card) 75%);
  }
  .brand {
    position: absolute;
    left: 40px;
    top: 58px;
    display: flex;
    align-items: center;
    gap: 12px;
    color: var(--gold);
    font-size: 22px;
    font-weight: 400;
    letter-spacing: 0.22em;
    text-transform: uppercase;
  }
  .brand .dot { width: 14px; height: 14px; }
  .person {
    position: absolute;
    left: 40px;
    top: 132px;
  }
  .person__name {
    color: var(--gold);
    font-size: 19px;
    font-weight: 700;
    letter-spacing: 0.02em;
    text-transform: uppercase;
  }
  .person__title {
    color: var(--ink-light);
    font-size: 12px;
    margin-top: 3px;
    letter-spacing: 0.04em;
  }
  .contact {
    position: absolute;
    left: 40px;
    top: 200px;
    list-style: none;
  }
  .contact__item {
    display: flex;
    align-items: center;
    gap: 12px;
    color: var(--ink-light);
    font-size: 12px;
    letter-spacing: 0.05em;
    height: 24px;
  }
  .contact__icon { width: 14px; height: 14px; flex: none; }
</style>
</head>
<body>

  <section class="card card-back" aria-label="Card back">
    <div class="card-back__pattern" role="img" aria-label="Tone-on-tone repeating bee pattern in spot UV across the card, brightest at the lower left"></div>
    <div class="card-back__mark">
      <span class="dot"></span>
      <span>Rima Vale Honey</span>
    </div>
  </section>

  <section class="card card-front" aria-label="Card front">
    <div class="card-front__emboss" role="img" aria-label="Large embossed bee motif in dark grey tone"></div>

    <div class="brand">
      <span class="dot"></span>
      <span>Rima Vale Honey</span>
    </div>

    <div class="person">
      <p class="person__name">Martin Holloway</p>
      <p class="person__title">Creative Director</p>
    </div>

    <ul class="contact">
      <li class="contact__item">
        <svg class="contact__icon" viewBox="0 0 14 14" aria-hidden="true">
          <circle cx="7" cy="7" r="7" fill="var(--gold)"/>
          <path d="M4.3 3.8l1.4-.3.8 1.7-.9.7c.4.9 1.1 1.6 2 2l.7-.9 1.7.8-.3 1.4c-3 .2-5.6-2.4-5.4-5.4z" fill="var(--card)"/>
        </svg>
        <span>+64 2815 96 417</span>
      </li>
      <li class="contact__item">
        <svg class="contact__icon" viewBox="0 0 14 14" aria-hidden="true">
          <circle cx="7" cy="7" r="7" fill="var(--gold)"/>
          <rect x="3.5" y="4.5" width="7" height="5" fill="var(--card)"/>
          <path d="M3.5 4.5L7 7.4l3.5-2.9" stroke="var(--gold)" stroke-width="0.8" fill="none"/>
        </svg>
        <span>martin@rimavalehoney.example.nz</span>
      </li>
      <li class="contact__item">
        <svg class="contact__icon" viewBox="0 0 14 14" aria-hidden="true">
          <circle cx="7" cy="7" r="7" fill="var(--gold)"/>
          <circle cx="7" cy="7" r="3.6" fill="none" stroke="var(--card)" stroke-width="0.9"/>
          <ellipse cx="7" cy="7" rx="1.5" ry="3.6" fill="none" stroke="var(--card)" stroke-width="0.8"/>
          <line x1="3.4" y1="7" x2="10.6" y2="7" stroke="var(--card)" stroke-width="0.8"/>
        </svg>
        <span>www.rimavalehoney.example.nz</span>
      </li>
    </ul>
  </section>

</body>
</html>
```